Desktop and Mobile Home Page Redesign

Please tailor the attached wireframe i made with your own design.
The key is to have the social icons being prominent, then have effectively 3 rows of mis-leveled posts to track the eye down the page.
At the bottom, I would like for you to design the same post types that dailyvortle.com.au have (attached) - I did not have time to add it into the wire frame.
Please design your own elements rather than taking from other sites direct.
Check out pelinora.com.au
We need a home page design for mobile and desktop (adaptive)
Must have features (desktop)
- Call to action buttons (large and attractive eg "Get More")
- The new redesign must be familiar to the old
- The design must have elements that prompt the user to scroll down e.g the video tab on the left of http://quorbit.com.au/ which forces the eye down
- Must have image galleries incorporated on the home page
-Must have room for 2 350x250 banners, 2 160x600 banners and 2 728x90 banners
- Must have originally formatted content in the middle of the page that would encourage navigation DEEP into the site (e.g think about how to format posts, polls, sliders, lists, galleries, videos, categories and menus, star rating)
- Must keep footer
- Must be adaptive
- Must have large and prominent share icons for each article and piece of content
- Must have a way to easily view comments
Must have features (mobile)
- Adaptive to zentrix and vaLphone
- Adaptive to both horizontal and vertical
- Easy tapping ability (finger size)
-Must have room for mobile banners
Updates
Target Market(s)
Females
Industry/Entity Type
Tailor
Requirements
Must have
- Check out pelinora.com.au
- Hero post
- Must keep footer
- Must be adaptive

```html
<!DOCTYPE html>
<html lang="en">
<head>
<meta charset="utf-8">
<title>Pelinora — Home</title>
<link href="https://fonts.googleapis.com/css2?family=Open+Sans:wght@400;600;700;800&family=Oswald:wght@500;700&display=swap" rel="stylesheet">
<style>
:root{
  --orange:#f58220;--orange-dark:#d96a0f;--green:#5db43a;--green-dark:#469a27;
  --blue:#2b8fd0;--navy:#1b2a47;--navy-2:#14203a;--ink:#2f2f2f;--muted:#7a7a7a;
  --line:#e3e3e3;--bg:#e9ecf0;--white:#fff;--yellow:#f7c51e;--pill:#e9eef6;
}
*{box-sizing:border-box;margin:0;padding:0}
html,body{width:1200px;height:2836px;overflow:hidden}
body{background:var(--bg);font-family:"Open Sans",Arial,sans-serif;color:var(--ink);font-size:13px;line-height:1.45}
a{color:inherit;text-decoration:none}
ul{list-style:none}
.site{position:absolute;left:120px;top:0;width:960px;height:2388px;background:var(--white);box-shadow:0 0 14px rgba(0,0,0,.12)}
.ph{display:block;border-radius:2px}
/* top bar */
.topbar{height:32px;padding:0 16px;display:flex;align-items:center;gap:10px;font-size:10px;font-weight:700;color:var(--muted);border-bottom:1px solid var(--line)}
/* header */
.masthead{height:108px;padding:0 16px;display:flex;align-items:center;justify-content:space-between}
.brand{display:flex;flex-direction:column}
.brand-name{font-family:"Open Sans",sans-serif;font-weight:800;font-size:34px;color:var(--navy);letter-spacing:-.5px;display:flex;align-items:center;gap:10px}
.brand-name i{width:14px;height:14px;background:var(--orange);display:inline-block}
.brand-tag{font-size:12px;color:var(--orange);font-style:italic;margin-left:24px}
.leaderboard{width:728px;height:90px;display:flex;background:#f3f3f3;border:1px solid var(--line)}
.leaderboard .ph{width:300px;height:100%;background:linear-gradient(135deg,#c9b6a4,#8f9fb0)}
.leaderboard .copy{flex:1;background:var(--yellow);padding:14px 18px;font-family:"Oswald",sans-serif;font-weight:700;font-size:22px;line-height:1.1;color:#222;display:flex;justify-content:space-between;align-items:center}
.leaderboard .copy small{display:block;font-family:"Open Sans",sans-serif;font-size:11px;font-weight:600}
.bank{font-family:"Open Sans",sans-serif;font-weight:800;font-size:18px;display:flex;align-items:center;gap:6px;color:#111}
.bank i{width:16px;height:16px;background:#111;display:inline-block}
/* nav */
.mainnav{height:40px;background:var(--orange);margin:4px 0 0;display:flex;padding:0 16px}
.mainnav a{color:#fff;font-weight:700;font-size:13px;padding:0 14px;line-height:40px;border-right:1px solid rgba(255,255,255,.3)}
.mainnav a.on{background:var(--orange-dark)}
.subnav{height:38px;display:flex;align-items:center;padding:0 16px;border-bottom:1px solid var(--line);font-size:10px;font-weight:700;color:#555}
.subnav a{padding:0 12px;border-right:1px solid var(--line)}
/* layout */
.wrap{padding:0 16px}
.row{display:flex;gap:18px}
.main{width:570px}
.aside{width:340px}
/* hero */
.hero-row{margin-top:18px;height:260px}
.hero{position:relative;height:260px;background:linear-gradient(135deg,#d9c6ae,#a4b59a 55%,#6d8a6a)}
.hero .dots{position:absolute;right:14px;bottom:10px;display:flex;gap:6px}
.hero .dots i{width:9px;height:9px;border-radius:50%;background:rgba(255,255,255,.6)}
.hero .dots i.on{background:#fff}
.mrec{height:250px;background:var(--yellow);position:relative;padding:22px;font-family:"Oswald",sans-serif;font-weight:700;font-size:22px;line-height:1.15;color:#222}
.mrec .ph{position:absolute;left:0;bottom:0;width:200px;height:110px;background:linear-gradient(135deg,#e4b98d,#b58d6a)}
.mrec .more{font-family:"Open Sans",sans-serif;font-size:11px;font-weight:700;margin-top:10px}
.mrec .bank{position:absolute;right:18px;bottom:20px}
/* row 2 */
.block2{margin-top:20px;height:800px}
.rail{width:150px}
.rail li{height:160px}
.rail .ph{width:150px;height:108px;background:linear-gradient(135deg,#c5b3a0,#8ea2b4)}
.rail p{font-size:11px;font-weight:600;text-align:center;margin-top:6px;color:#555}
.center{width:402px}
.feature{display:flex;gap:14px;height:180px}
.feature .ph{width:190px;height:170px;background:linear-gradient(135deg,#e3cdb8,#9fb3c3)}
.feature h2{font-size:21px;line-height:1.2;font-weight:800;color:var(--navy)}
.feature p{font-size:10px;color:var(--muted);margin-top:8px}
.share{display:flex;gap:5px;margin-top:6px}
.share span{font-size:9px;font-weight:700;padding:2px 8px;border-radius:2px;background:var(--pill);color:#3a5b8c;border:1px solid #cdd7e6}
.list li{display:flex;gap:10px;height:56px;margin-top:6px}
.list .ph{width:52px;height:48px;background:linear-gradient(135deg,#d7bfa9,#a9b8c6)}
.list b{font-size:11px;display:block}
.sec-title{font-family:"Oswald",sans-serif;font-weight:700;font-size:18px;color:var(--navy);text-transform:uppercase;border-bottom:2px solid var(--line);padding-bottom:4px;margin:18px 0 12px}
.sec-title.hot{color:var(--orange)}
.bloggers{display:grid;grid-template-columns:1fr 1fr;gap:16px 16px}
.blogger{display:flex;gap:10px;height:70px}
.blogger .ph{width:64px;height:64px;background:linear-gradient(135deg,#dcc2aa,#9aaebf)}
.blogger b{font-size:12px;display:block}
.blogger p{font-size:10px;color:var(--muted)}
/* aside */
.cta{display:flex;justify-content:space-between;align-items:center;height:48px;background:var(--green);color:#fff;font-weight:800;font-size:18px;padding:0 16px;border-radius:3px;box-shadow:inset 0 -3px 0 var(--green-dark)}
.cta svg{width:22px;height:22px}
.newsletter{margin-top:12px;background:var(--blue);padding:12px 14px;height:96px;color:#fff}
.newsletter h3{font-size:14px;font-weight:800}
.newsletter form{display:flex;margin-top:10px}
.newsletter input{flex:1;height:32px;border:0;padding:0 10px;font:11px "Open Sans",sans-serif}
.newsletter button{width:50px;height:32px;border:0;background:var(--navy);color:#fff;font-weight:700;font-size:11px}
.aside .sec-title{margin-top:20px}
.gallery{display:grid;grid-template-columns:repeat(4,1fr);gap:6px}
.gallery i{height:74px;display:block;background:linear-gradient(135deg,#d8c1ab,#8fa5b8)}
.gallery i:nth-child(3n){background:linear-gradient(135deg,#b9c9b0,#7f9a86)}
.gallery i:nth-child(4n+2){background:linear-gradient(135deg,#e1c9c0,#b68f86)}
.community{margin-top:20px;border:1px solid #c9d3e2;height:330px;padding:12px}
.community-head{display:flex;align-items:center;gap:8px;font-weight:800;font-size:14px;color:var(--navy)}
.community-head i{width:36px;height:36px;background:var(--orange);display:inline-block}
.community-head span.like{margin-left:auto;font-size:10px;padding:3px 10px;background:var(--pill);border:1px solid #cdd7e6;color:#3a5b8c}
.community p{font-size:10px;color:var(--muted);margin:10px 0}
.faces{display:grid;grid-template-columns:repeat(5,1fr);gap:6px}
.faces i{height:52px;display:block;background:linear-gradient(135deg,#d5c0ad,#a0aec0)}
/* talking */
.block3{height:900px}
.talk{display:grid;grid-template-columns:1fr 1fr;gap:22px 22px}
.post{display:flex;gap:10px;height:100px}
.post .ph{width:84px;height:74px;background:linear-gradient(135deg,#dbc3ac,#98adbf)}
.post b{font-size:12px;display:block}
.post p{font-size:10px;color:var(--muted)}
.skys{display:flex;gap:20px;margin-top:60px}
.sky{width:160px}
.sky-a{height:360px;background:linear-gradient(160deg,#2a3a26,#4b6b3a);padding:14px;color:#e9f36a;font-family:"Oswald",sans-serif;font-weight:700;font-size:22px;line-height:1.15}
.sky-a small{display:block;margin-top:150px;font-family:"Open Sans",sans-serif;font-size:10px;color:#fff}
.sky-b{height:470px;margin-top:10px;background:linear-gradient(180deg,#9ccf5c,#3f8a2c)}
.sky-c{height:840px;background:linear-gradient(180deg,#c9d12a,#b3262b 35%,#1d1d1d 70%,#6a7c24);padding:16px 10px;color:#fff;font-family:"Oswald",sans-serif;font-weight:700;text-align:center;font-size:26px;line-height:1.05}
.sky-c small{display:block;font-size:16px;margin-top:420px}
.comments{display:grid;grid-template-columns:repeat(4,1fr);gap:14px}
.comment .ph{height:94px;background:linear-gradient(135deg,#d9c4b0,#94a9bc)}
.comment b{display:block;font-size:12px;margin-top:6px}
.comment p{font-size:10px;color:var(--muted)}
.comment .more{display:inline-block;margin-top:6px;font-size:10px;font-weight:800;color:var(--orange)}
.foot-banner{margin:26px auto 0;width:728px;height:80px;display:flex;background:#e9f5ec;border:1px solid var(--line)}
.foot-banner .ph{width:220px;height:100%;background:linear-gradient(135deg,#d0bfae,#9db4a2)}
.foot-banner span{flex:1;display:flex;align-items:center;padding-left:24px;font-family:"Oswald",sans-serif;font-size:22px;font-weight:500;color:var(--green-dark)}
/* footer */
.site-footer{position:absolute;left:0;top:2388px;width:1200px;height:448px;background:var(--navy);color:#c9d2e2}
.footer-inner{width:960px;margin:0 auto;padding:36px 16px 0;display:flex;gap:30px}
.footer-inner h4{color:#fff;font-size:15px;margin-bottom:10px}
.footer-inner li{font-size:11px;line-height:2}
.fcol{width:170px}
.social{display:flex;gap:6px;margin-top:10px}
.social i{width:24px;height:24px;border-radius:50%;background:#fff;opacity:.85;display:block}
.legal{position:absolute;left:0;bottom:0;width:1200px;height:42px;background:var(--navy-2);font-size:10px;color:#8b97ad}
.legal p{width:960px;margin:0 auto;padding:14px 16px}
</style>
</head>
<body>
<div class="site">
  <div class="topbar"><a href="#">REGISTER</a><span>|</span><a href="#">LOG IN</a></div>

  <header class="masthead">
    <a class="brand" href="#">
      <span class="brand-name"><i></i>Pelinora</span>
      <span class="brand-tag">What women are talking about</span>
    </a>
    <div class="leaderboard">
      <span class="ph" role="img" aria-label="Advert photo of smiling young savers"></span>
      <div class="copy"><div>ENJOY A 4.00% BONUS RATE<small>Conditions apply. Find out more</small></div><span class="bank"><i></i>KORRA</span></div>
    </div>
  </header>

  <nav class="mainnav">
    <a class="on" href="#">HOME</a><a href="#">NEWS</a><a href="#">STYLE</a><a href="#">SOCIAL</a><a href="#">RELATIONSHIPS</a><a href="#">ENTERTAINMENT</a><a href="#">PARENTING</a><a href="#">FOOD</a><a href="#">WELLBEING</a>
  </nav>
  <nav class="subnav">
    <a href="#">PRODUCT REVIEWS</a><a href="#">TRAVEL</a><a href="#">GALLERIES</a><a href="#">VIDEOS</a><a href="#">PELINORA LIKES</a><a href="#">ABOUT/ADVERTISE</a><a href="#">CONTACT</a>
  </nav>

  <div class="wrap">
    <div class="row hero-row">
      <section class="main hero" role="img" aria-label="Hero slide: a father and child decorating a Christmas tree">
        <div class="dots"><i class="on"></i><i></i><i></i><i></i></div>
      </section>
      <aside class="aside mrec">
        FOR A GREAT START.<br>OPEN A STARTERSAVER<br>ACCOUNT TODAY.
        <div class="more">Find out more ›</div>
        <span class="ph" role="img" aria-label="Advert photo of a young boy with a piggy bank"></span>
        <span class="bank"><i></i>KORRA</span>
      </aside>
    </div>

    <div class="row block2">
      <div class="main row" style="gap:18px">
        <ul class="rail">
          <li><span class="ph" role="img" aria-label="Photo from a community rally"></span><p>Photo rally pics from the weekend</p></li>
          <li><span class="ph" role="img" aria-label="Photo from a community rally"></span><p>Photo rally pics from the city</p></li>
          <li><span class="ph" role="img" aria-label="Photo from a community rally"></span><p>Photo rally pics you sent us</p></li>
          <li><span class="ph" role="img" aria-label="Photo from a community rally"></span><p>Photo rally pics by readers</p></li>
          <li><span class="ph" role="img" aria-label="Photo from a community rally"></span><p>Photo rally pics of the week</p></li>
        </ul>
        <div class="center">
          <article class="feature">
            <span class="ph" role="img" aria-label="Photo of a father holding his newborn baby"></span>
            <div>
              <h2>Doctor says: Men should NEVER watch women give birth</h2>
              <p>By Pelinora staff. A leading obstetrician argues partners should stay at the head of the bed during labour.</p>
              <div class="share"><span>Share</span><span>Post</span><span>Email</span></div>
            </div>
          </article>
          <ul class="list">
            <li><span class="ph" role="img" aria-label="Story thumbnail photo"></span><div><b>Class aptent taciti sociosqu ad litora</b><div class="share"><span>Share</span><span>Post</span><span>Email</span></div></div></li>
            <li><span class="ph" role="img" aria-label="Story thumbnail photo"></span><div><b>Class aptent taciti sociosqu ad litora</b><div class="share"><span>Share</span><span>Post</span><span>Email</span></div></div></li>
            <li><span class="ph" role="img" aria-label="Story thumbnail photo"></span><div><b>Class aptent taciti sociosqu ad litora</b><div class="share"><span>Share</span><span>Post</span><span>Email</span></div></div></li>
          </ul>
          <h3 class="sec-title">Pelinora Bloggers</h3>
          <div class="bloggers">
            <div class="blogger"><span class="ph" role="img" aria-label="Blogger portrait"></span><div><b>Blog Title</b><p>Fresh thoughts on family, work and the week ahead.</p></div></div>
            <div class="blogger"><span class="ph" role="img" aria-label="Blogger portrait"></span><div><b>Blog Title</b><p>Fresh thoughts on family, work and the week ahead.</p></div></div>
            <div class="blogger"><span class="ph" role="img" aria-label="Blogger portrait"></span><div><b>Blog Title</b><p>Fresh thoughts on family, work and the week ahead.</p></div></div>
            <div class="blogger"><span class="ph" role="img" aria-label="Blogger portrait"></span><div><b>Blog Title</b><p>Fresh thoughts on family, work and the week ahead.</p></div></div>
            <div class="blogger"><span class="ph" role="img" aria-label="Blogger portrait"></span><div><b>Blog Title</b><p>Fresh thoughts on family, work and the week ahead.</p></div></div>
            <div class="blogger"><span class="ph" role="img" aria-label="Blogger portrait"></span><div><b>Blog Title</b><p>Fresh thoughts on family, work and the week ahead.</p></div></div>
          </div>
        </div>
      </div>
      <aside class="aside">
        <a class="cta" href="#">GET STARTED NOW
          <svg viewBox="0 0 24 24"><circle cx="12" cy="12" r="11" fill="#fff"/><path d="M10 7l5 5-5 5" stroke="#5db43a" stroke-width="2.6" fill="none" stroke-linecap="round"/></svg>
        </a>
        <div class="newsletter">
          <h3>SIGN UP NEWSLETTER</h3>
          <form><input type="text" placeholder="email address"><button type="button">GO</button></form>
        </div>
        <h3 class="sec-title">Photo Gallery</h3>
        <div class="gallery">
          <i role="img" aria-label="Gallery photo"></i><i role="img" aria-label="Gallery photo"></i><i role="img" aria-label="Gallery photo"></i><i role="img" aria-label="Gallery photo"></i>
          <i role="img" aria-label="Gallery photo"></i><i role="img" aria-label="Gallery photo"></i><i role="img" aria-label="Gallery photo"></i><i role="img" aria-label="Gallery photo"></i>
          <i role="img" aria-label="Gallery photo"></i><i role="img" aria-label="Gallery photo"></i><i role="img" aria-label="Gallery photo"></i><i role="img" aria-label="Gallery photo"></i>
        </div>
        <div class="community">
          <div class="community-head"><i></i>Pelinora<span class="like">Like</span></div>
          <p>48,210 people like Pelinora</p>
          <div class="faces">
            <i role="img" aria-label="Reader avatar"></i><i role="img" aria-label="Reader avatar"></i><i role="img" aria-label="Reader avatar"></i><i role="img" aria-label="Reader avatar"></i><i role="img" aria-label="Reader avatar"></i>
            <i role="img" aria-label="Reader avatar"></i><i role="img" aria-label="Reader avatar"></i><i role="img" aria-label="Reader avatar"></i><i role="img" aria-label="Reader avatar"></i><i role="img" aria-label="Reader avatar"></i>
            <i role="img" aria-label="Reader avatar"></i><i role="img" aria-label="Reader avatar"></i><i role="img" aria-label="Reader avatar"></i><i role="img" aria-label="Reader avatar"></i><i role="img" aria-label="Reader avatar"></i>
            <i role="img" aria-label="Reader avatar"></i><i role="img" aria-label="Reader avatar"></i><i role="img" aria-label="Reader avatar"></i><i role="img" aria-label="Reader avatar"></i><i role="img" aria-label="Reader avatar"></i>
          </div>
          <p>Community plugin</p>
        </div>
      </aside>
    </div>

    <div class="row block3">
      <div class="main">
        <h3 class="sec-title hot">Today we're talking about</h3>
        <div class="talk">
          <div class="post"><span class="ph" role="img" aria-label="Post thumbnail"></span><div><b>Blog Title</b><p>Maecenas aliquet velit vel turpis, sed tempus nibh porta quis lorem.</p><div class="share"><span>Share</span><span>Post</span><span>Email</span></div></div></div>
          <div class="post"><span class="ph" role="img" aria-label="Post thumbnail"></span><div><b>Blog Title</b><p>Maecenas aliquet velit vel turpis, sed tempus nibh porta quis lorem.</p><div class="share"><span>Share</span><span>Post</span><span>Email</span></div></div></div>
          <div class="post"><span class="ph" role="img" aria-label="Post thumbnail"></span><div><b>Blog Title</b><p>Maecenas aliquet velit vel turpis, sed tempus nibh porta quis lorem.</p><div class="share"><span>Share</span><span>Post</span><span>Email</span></div></div></div>
          <div class="post"><span class="ph" role="img" aria-label="Post thumbnail"></span><div><b>Blog Title</b><p>Maecenas aliquet velit vel turpis, sed tempus nibh porta quis lorem.</p><div class="share"><span>Share</span><span>Post</span><span>Email</span></div></div></div>
          <div class="post"><span class="ph" role="img" aria-label="Post thumbnail"></span><div><b>Blog Title</b><p>Maecenas aliquet velit vel turpis, sed tempus nibh porta quis lorem.</p><div class="share"><span>Share</span><span>Post</span><span>Email</span></div></div></div>
          <div class="post"><span class="ph" role="img" aria-label="Post thumbnail"></span><div><b>Blog Title</b><p>Maecenas aliquet velit vel turpis, sed tempus nibh porta quis lorem.</p><div class="share"><span>Share</span><span>Post</span><span>Email</span></div></div></div>
          <div class="post"><span class="ph" role="img" aria-label="Post thumbnail"></span><div><b>Blog Title</b><p>Maecenas aliquet velit vel turpis, sed tempus nibh porta quis lorem.</p><div class="share"><span>Share</span><span>Post</span><span>Email</span></div></div></div>
          <div class="post"><span class="ph" role="img" aria-label="Post thumbnail"></span><div><b>Blog Title</b><p>Maecenas aliquet velit vel turpis, sed tempus nibh porta quis lorem.</p><div class="share"><span>Share</span><span>Post</span><span>Email</span></div></div></div>
        </div>

        <h3 class="sec-title hot" style="margin-top:56px">Recent comments</h3>
        <div class="comments">
          <div class="comment"><span class="ph" role="img" aria-label="Article photo"></span><b>Blog Title</b><p>Maecenas aliquet velit vel turpis sed tempus nibh porta.</p><a class="more" href="#">LEARN MORE</a></div>
          <div class="comment"><span class="ph" role="img" aria-label="Article photo"></span><b>Blog Title</b><p>Maecenas aliquet velit vel turpis sed tempus nibh porta.</p><a class="more" href="#">LEARN MORE</a></div>
          <div class="comment"><span class="ph" role="img" aria-label="Article photo"></span><b>Blog Title</b><p>Maecenas aliquet velit vel turpis sed tempus nibh porta.</p><a class="more" href="#">LEARN MORE</a></div>
          <div class="comment"><span class="ph" role="img" aria-label="Article photo"></span><b>Blog Title</b><p>Maecenas aliquet velit vel turpis sed tempus nibh porta.</p><a class="more" href="#">LEARN MORE</a></div>
        </div>
      </div>
      <aside class="aside skys">
        <div class="sky">
          <div class="sky-a">Do you give a Brennick?<small>Help us get Brennick now</small></div>
          <div class="sky-b" role="img" aria-label="Advert: large green leaf for a walking trail map"></div>
        </div>
        <div class="sky sky-c">NATION OF<br>STATIC<br>ORBIT<small>NIGHT SIGNAL<br>COMING 2013</small></div>
      </aside>
    </div>

    <div class="foot-banner">
      <span class="ph" role="img" aria-label="Advert photo of schoolchildren"></span>
      <span>Help us make school funding fairer ›</span>
    </div>
  </div>
</div>

<footer class="site-footer">
  <div class="footer-inner">
    <div class="fcol"><h4>Information</h4><ul><li>Home</li><li>Advertise with us</li><li>About</li><li>FAQs</li><li>Archives</li><li>Competitions &amp; Giveaways</li><li>Site Map</li><li>Work with us</li><li>Privacy Policy</li><li>Contact us</li></ul></div>
    <div class="fcol"><h4>Topics</h4><ul><li>Dating</li><li>Sex</li><li>Weddings &amp; Marriage</li><li>Gay and Lesbian</li><li>Boutique</li><li>Friendships</li><li>Ageing</li><li>Men</li><li>Women</li></ul></div>
    <div class="fcol"><h4>&nbsp;</h4><ul><li>Motherhood</li><li>Fatherhood</li><li>Pregnancy</li><li>Birth</li><li>Breastfeeding</li><li>Career Affairs</li><li>Childcare</li><li>Body Image and Retouching</li><li>Politics &amp; World</li></ul></div>
    <div class="fcol"><h4>&nbsp;</h4><ul><li>Career &amp; Money</li><li>Style</li><li>Fashion</li><li>Beauty</li><li>Lifestyle</li><li>Recipes</li><li>Nutrition</li><li>Wellbeing</li><li>Celebrity</li></ul></div>
    <div class="fcol"><h4>&nbsp;</h4><ul><li>Books</li><li>Movies</li><li>Technology and Gadgets</li><li>Social Media</li></ul>
      <div class="social"><i aria-label="Social link"></i><i aria-label="Social link"></i><i aria-label="Social link"></i><i aria-label="Social link"></i></div>
    </div>
  </div>
  <div class="legal"><p>© 2013 Pelinora Media. All rights reserved. Terms of Use</p></div>
</footer>
</body>
</html>
```